Investor Presentation

We have a deck that is mostly finished that needs to be properly formatted and cleaned up. The presentation is for an investment in a financial firm. So the design we are looking for is very professional and minimalistic. A very clean look with conservative color schemes and fonts. The designer can leverage our existing logos, background, etc.

The final design files should have full editing functionality.

Target Market(s)

Sophisticated institutional investors

Industry/Entity Type

Conservative

Requirements
Nice to have
• Cleaned up / formatted tables from the attached files to add to the presentation.

```html
<!DOCTYPE html>
<html lang="en">
<head>
<meta charset="UTF-8">
<title>Table data Heading</title>
<link rel="stylesheet" href="https://fonts.googleapis.com/css2?family=Open+Sans:wght@400&family=Roboto:wght@400;500&family=Ubuntu:wght@400;500&display=swap">
<style>
  :root {
    --header-teal: #027479;
    --table-head: #2a959c;
    --footer-teal: #3594a0;
    --row-grey: #eae9e7;
    --row-aqua: #9fdfe5;
    --subtitle: #00777b;
    --ink: #333333;
    --white: #ffffff;
  }
  * { box-sizing: border-box; margin: 0; padding: 0; }
  html, body { width: 1200px; height: 900px; overflow: hidden; background: var(--white); }
  .slide { position: relative; width: 1200px; height: 900px; background: var(--white); }

  .slide-header {
    position: absolute; left: 0; top: 0; width: 1200px; height: 99px;
    background: var(--header-teal);
  }
  .slide-title {
    position: absolute; left: 27px; top: 24px;
    font-family: "Ubuntu", sans-serif; font-weight: 400; font-size: 42px;
    color: var(--white); line-height: 1.2;
  }
  .brand {
    position: absolute; right: 15px; top: 42px;
    display: flex; align-items: center; gap: 12px;
  }
  .brand-dot { width: 20px; height: 20px; border-radius: 50%; background: var(--white); }
  .brand-name {
    font-family: "Ubuntu", sans-serif; font-weight: 400; font-size: 24px;
    color: var(--white); line-height: 1;
  }

  .intro { position: absolute; left: 60px; top: 154px; width: 1080px; }
  .intro-subtitle {
    font-family: "Roboto", sans-serif; font-weight: 500; font-size: 24px;
    color: var(--subtitle); line-height: 1.3;
  }
  .intro-body {
    margin-top: 17px;
    font-family: "Roboto", sans-serif; font-size: 18px; line-height: 28.5px;
    color: var(--ink);
  }

  .data-table {
    position: absolute; left: 60px; top: 303px; width: 1085px;
    border-collapse: separate; border-spacing: 0 6px; margin-top: -6px;
    table-layout: fixed;
    font-family: "Roboto", sans-serif; text-align: center;
  }
  .data-table th {
    height: 63px; background: var(--table-head); color: var(--white);
    font-weight: 500; font-size: 27px; text-transform: uppercase;
  }
  .data-table td {
    height: 56px; font-size: 22px; color: var(--ink);
  }
  .data-table tr.row-grey td { background: var(--row-grey); }
  .data-table tr.row-aqua td { background: var(--row-aqua); }

  .slide-footer {
    position: absolute; left: 0; top: 856px; width: 1200px; height: 44px;
    background: var(--footer-teal);
  }
  .copyright {
    position: absolute; left: 12px; top: 10px;
    font-family: "Open Sans", sans-serif; font-size: 19px; color: var(--white);
  }
</style>
</head>
<body>
<div class="slide">
  <header class="slide-header">
    <h1 class="slide-title">Table data Heading</h1>
    <div class="brand">
      <span class="brand-dot"></span>
      <span class="brand-name">Halvern Capital, LLC</span>
    </div>
  </header>

  <section class="intro">
    <h2 class="intro-subtitle">Table Subtitle Here</h2>
    <p class="intro-body">Lorem ipsum dolor sit Lorem ipsum dolor sit&nbsp; Lorem ipsum dolor sit Lorem ipsum dolor sit&nbsp; Lorem ipsum dolor sit Lorem ipsum dolor sit&nbsp; Lorem ipsum dolor sit Lorem ipsum dolor sit&nbsp; Lorem ipsum dolor sit Lorem ipsum dolor sit&nbsp; Lorem ipsum dolor sit Lorem ipsum dolor sit&nbsp; Lorem ipsum dolor sit Lorem ipsum dolor sit&nbsp; Lorem ipsum dolor sit Lorem ipsum dolor sit</p>
  </section>

  <table class="data-table">
    <thead>
      <tr><th>Table Title Here</th><th>Table Title Here</th><th>Table Title Here</th></tr>
    </thead>
    <tbody>
      <tr class="row-grey"><td>Subtext here</td><td>Subtext here</td><td>Subtext here</td></tr>
      <tr class="row-aqua"><td>Subtext here</td><td>Subtext here</td><td>Subtext here</td></tr>
      <tr class="row-grey"><td>Subtext here</td><td>Subtext here</td><td>Subtext here</td></tr>
      <tr class="row-aqua"><td>Subtext here</td><td>Subtext here</td><td>Subtext here</td></tr>
      <tr class="row-grey"><td>Subtext here</td><td>Subtext here</td><td>Subtext here</td></tr>
      <tr class="row-aqua"><td>Subtext here</td><td>Subtext here</td><td>Subtext here</td></tr>
    </tbody>
  </table>

  <footer class="slide-footer">
    <p class="copyright">Copyright text here</p>
  </footer>
</div>
</body>
</html>
```